Hull Harbour Trade Website makeover

Hull Harbour Trade is in need of a makeover. It is feeling tired and needs a fresh new look and feel as well as being user friendly.

Hull Harbour Trade is an industry owned marketplace website for the sale of recreational boats, marina berths, chandlery, water craft like kayaks - anything related to recreation on the water. The main focus however is boats - new and used. The site is only available to industry businesses so no private sales are available on the site.

This approach ensures that the buyers know that title is guaranteed to all boats sold and that the businesses are reputable and stand behind their products.

The current site address is www.hullharbourtrade.com.au

Target Market(s)

The target market are people interested in outdoor recreation - boaters, kayakers, sailors, paddle boarders, those looking for marina berths for their boat and those looking for service providers.

It should appeal to families, males and females, sports oriented people, fishermen, and those just looking for a relaxing, outdoor, healthy lifestyle.

Requirements
Must have
• Be very user friendly, intuitive in terms of searching, be uncluttered, fresh and engaging.
• Marine recreation is about lifestyle, fun and relaxation. When people buy a boat they are buying into a desirable, healthy lifestyle.
• It must present as professional and give consumers confidence about the professionalism of the businesses selling their products on the site.
Nice to have
• Good images that portray the lifestyle in the Australian marketplace.
• Cater for the needs of sellers to be able to showcase their products to consumers.
Should not have
• Be cluttered and hard to navigate.

```html
<!DOCTYPE html>
<html lang="en">
<head>
<meta charset="utf-8">
<title>Hull Harbour Trade – Testimonials and About Us</title>
<link href="https://fonts.googleapis.com/css2?family=Fira+Sans:ital,wght@0,500;1,400;1,600&display=swap" rel="stylesheet">
<style>
  :root {
    --page-bg: #f3f3f3;
    --text-grey: #a9a9a9;
    --quote-grey: #c9c9c9;
    --heading-grey: #8d8d8d;
    --accent-blue: #5daee6;
    --frame-grey: #dcdcdc;
    --rule-grey: #bdbdbd;
    --banner-light: #9fd2f4;
    --banner-mid: #4a9fe0;
  }
  * { box-sizing: border-box; margin: 0; padding: 0; }
  html, body { width: 1200px; height: 900px; overflow: hidden; }
  body {
    position: relative;
    background: var(--page-bg);
    font-family: "Fira Sans", Arial, sans-serif;
    color: var(--text-grey);
  }
  .body-copy {
    font-style: italic;
    font-weight: 400;
    font-size: 17px;
    line-height: 21.5px;
    letter-spacing: 0.35px;
    white-space: nowrap;
  }
  .quote-mark { position: absolute; width: 32px; height: 30px; }
  .testimonial-text { position: absolute; }
  .testimonial-author {
    position: absolute;
    font-style: italic;
    font-size: 14px;
    letter-spacing: 0.2px;
    color: var(--accent-blue);
    white-space: nowrap;
  }
  .portrait {
    position: absolute;
    width: 170px;
    height: 170px;
    border-radius: 50%;
    border: 9px solid var(--frame-grey);
    box-shadow: 0 1px 3px rgba(0,0,0,0.12);
  }
  .portrait-one { left: 848px; top: 51px; background: radial-gradient(circle at 55% 45%, #e9c3ad 0%, #d9a98e 40%, #f2f2f2 75%); }
  .portrait-two { left: 184px; top: 316px; background: radial-gradient(circle at 45% 45%, #e3b79c 0%, #cf9a7b 40%, #eef0f2 75%); }

  .section-heading {
    position: absolute;
    left: 0; top: 558px; width: 1200px;
    text-align: center;
    font-weight: 500;
    font-size: 24px;
    color: var(--heading-grey);
    text-shadow: 0 1px 0 #fff;
  }
  .heading-rule { position: absolute; top: 571px; height: 3px; border-radius: 2px; }
  .heading-rule-left { left: 190px; width: 241px; background: linear-gradient(to right, rgba(189,189,189,0), var(--rule-grey)); }
  .heading-rule-right { left: 751px; width: 250px; background: linear-gradient(to left, rgba(189,189,189,0), var(--rule-grey)); }

  .about-banner {
    position: absolute;
    left: 180px; top: 645px;
    width: 130px; height: 255px;
    background: linear-gradient(to right, var(--banner-light), var(--banner-mid));
  }

  .about-text { position: absolute; left: 336px; top: 647px; }
  .about-text p + p { margin-top: 21.5px; }
  .brand-name { color: var(--accent-blue); font-weight: 600; }
  .about-question {
    position: absolute; left: 336px; top: 833px;
    color: var(--accent-blue); font-weight: 600;
  }
  .about-more { position: absolute; left: 336px; top: 876px; }
</style>
</head>
<body>

<section class="testimonial testimonial-first">
  <svg class="quote-mark" style="left:197px;top:55px" viewBox="0 0 32 30" aria-hidden="true">
    <path fill="#c9c9c9" d="M0 30V17C0 7 4 2 12 0l1 4C8 6 6 9 6 13h7v17zM18 30V17C18 7 22 2 30 0l1 4c-5 2-7 5-7 9h7v17z"/>
  </svg>
  <p class="testimonial-text body-copy" style="left:243px;top:67px">
    Lorem ipsum dolor sit amet, consectetur adipisicing elit, sed do<br>
    eiusmod tempor incididunt ut labore et dolore magna aliqua. Ut enim ad<br>
    minim veniam, quis nostrud exercitation ullamco laboris nisi ut aliquip<br>
    ex ea commodo consequat. Duis aute irure dolor in reprehenderit in<br>
    voluptate velit esse cillum dolore eu fugiat nulla pariatur.
  </p>
  <p class="testimonial-author" style="right:379px;top:195px">By Lena Marsh</p>
  <div class="portrait portrait-one" role="img" aria-label="Portrait photo of a smiling woman, customer Lena Marsh"></div>
</section>

<section class="testimonial testimonial-second">
  <div class="portrait portrait-two" role="img" aria-label="Portrait photo of a smiling man, customer Owen Radley"></div>
  <svg class="quote-mark" style="left:398px;top:320px" viewBox="0 0 32 30" aria-hidden="true">
    <path fill="#c9c9c9" d="M0 30V17C0 7 4 2 12 0l1 4C8 6 6 9 6 13h7v17zM18 30V17C18 7 22 2 30 0l1 4c-5 2-7 5-7 9h7v17z"/>
  </svg>
  <p class="testimonial-text body-copy" style="left:444px;top:332px">
    Lorem ipsum dolor sit amet, consectetur adipisicing elit, sed do<br>
    eiusmod tempor incididunt ut labore et dolore magna aliqua. Ut enim ad<br>
    minim veniam, quis nostrud exercitation ullamco laboris nisi ut aliquip<br>
    ex ea commodo consequat. Duis aute irure dolor in reprehenderit in<br>
    voluptate velit esse cillum dolore eu fugiat nulla pariatur.
  </p>
  <p class="testimonial-author" style="right:176px;top:460px">By Owen Radley</p>
</section>

<section class="about">
  <div class="heading-rule heading-rule-left"></div>
  <h2 class="section-heading">ABOUT US</h2>
  <div class="heading-rule heading-rule-right"></div>

  <div class="about-banner" role="img" aria-label="Decorative blue stitched ribbon banner"></div>

  <div class="about-text body-copy">
    <p><span class="brand-name">HullHarbourTrade.com.au</span> is owned and operated by the Marine Trade Alliance (MTA) of<br>
    Australia. Hull Harbour Trade is the only online marine marketplace that offers the largest<br>
    range of boats for sale and other marine related products, backed by the associations and<br>
    their members.</p>
    <p>Here you'll find New and Used Boats for sale, Marina Berths and associated Marine<br>
    Products for sale, from right across the country and from respected Accredited Brokers,</p>
  </div>
  <h3 class="about-question body-copy">What will you get from subscribing to Hull Harbour Trade?</h3>
  <p class="about-more body-copy">A more cost effective, industry owned and operated website for the sale of boats, marina</p>
</section>

</body>
</html>
```